KAJU Freightways #ALLKAJU Business Cards & Letterhead

I am looking to business cards designed for our organization. We are currently undergoing a small re-branding that is taking place. Our organization is called KAJU Freightways and we are headquartered in Phoenix, AZ. We primarily provide transportation and logistics services to the Marlow Parcel Bureau who is our largest customer. I would like to see a design that incorporates name, title, contact info, website, and address (this will be different depending on the employee). I would also like to see some color on the business card using our logo colors or a variation. I would like our logo on the back of the business card with the website displayed. The final design should communicate that we are a next generation transportation operate that focuses on being driver-first, customer-centric, innovative, and sustainable.We would also like our #ALLKAJU catch phrase incorporated as well.

Target Market(s)

Transportation & Logistics

Industry/Entity Type

Trucking Company

Contact Information for Business Card

-First and Last Name
-Position Title
-Contact Phone
-Contact Email
-Physical Address

Font styles to use
Serif

Colors

Designer to choose colors to be used in the design.

Requirements
Must have
• -KAJU logo prominently displayed
• -#ALLKAJU catch phrase used
• -Some amount of color, design gradient, etc.
• -Logo on the back with website listed (https://www.kajufreightco.example)

```html
<!DOCTYPE html>
<html lang="en">
<head>
<meta charset="utf-8">
<title>KAJU Freightways Business Card</title>
<link rel="stylesheet" href="https://fonts.googleapis.com/css2?family=Roboto+Slab:wght@400;500;700&display=swap">
<style>
  :root {
    --backdrop: #b8b8b8;
    --card: #f1f1f0;
    --navy: #023643;
    --green: #74b62a;
    --ink: #1c3440;
  }
  * { margin: 0; padding: 0; box-sizing: border-box; }
  html, body { width: 1200px; height: 576px; overflow: hidden; }
  body {
    background: var(--backdrop);
    font-family: "Roboto Slab", Georgia, serif;
    position: relative;
  }
  .card {
    position: absolute;
    background: var(--card);
    border-radius: 8px;
    overflow: hidden;
    box-shadow: 0 3px 6px rgba(0,0,0,0.25);
  }

  .brand { display: flex; align-items: center; justify-content: center; gap: 12px; }
  .brand-name {
    font-family: "Roboto Slab", Georgia, serif;
    font-weight: 700; color: var(--navy); letter-spacing: 1px; line-height: 1;
  }
  .brand-dot { border-radius: 50%; background: var(--green); flex: none; }

  /* Back of card */
  .card-back { left: 82px; top: 139px; width: 484px; height: 293px; }
  .card-back .brand { position: absolute; left: 0; right: 0; top: 110px; }
  .card-back .brand-name { font-size: 54px; }
  .card-back .brand-dot { width: 20px; height: 20px; }
  .catchphrase {
    position: absolute; left: 0; right: 0; top: 178px;
    text-align: center; font-size: 13px; font-weight: 700;
    letter-spacing: 3px; color: var(--green);
  }
  .website-line {
    position: absolute; left: 0; right: 0; top: 250px;
    display: flex; align-items: center; justify-content: center; gap: 14px;
    font-size: 12.5px; letter-spacing: 1.4px; color: var(--ink);
  }
  .website-line .rule { width: 34px; height: 3px; background: var(--green); clip-path: polygon(0 50%, 100% 0, 100% 100%); }
  .website-line .rule.right { clip-path: polygon(0 0, 100% 50%, 0 100%); }
  .base-band { position: absolute; left: 0; right: 0; bottom: 0; height: 14px; display: flex; }
  .base-band .navy { flex: 1; background: var(--navy); }
  .base-band .green { flex: 1; background: var(--green); }

  /* Front of card */
  .card-front { left: 602px; top: 138px; width: 480px; height: 291px; }
  .card-front svg.wave { position: absolute; left: 0; top: 0; }
  .person { position: absolute; left: 22px; top: 20px; color: #fff; }
  .person-name { font-weight: 700; font-size: 19px; line-height: 1.2; }
  .person-title { font-size: 11.5px; margin-top: 4px; color: #e6eef0; }
  .service {
    position: absolute; left: 22px; top: 144px;
    font-size: 12px; font-weight: 700; color: var(--green);
  }
  .address {
    position: absolute; left: 22px; top: 170px;
    font-size: 12px; line-height: 19px; color: var(--ink); font-style: normal;
  }
  .contacts { position: absolute; left: 22px; top: 220px; list-style: none; font-size: 12px; color: var(--ink); }
  .contacts li { display: flex; align-items: center; gap: 12px; height: 18.5px; }
  .contacts svg { width: 12px; height: 12px; flex: none; }
  .card-front .brand { position: absolute; left: 270px; top: 160px; width: 190px; gap: 10px; }
  .card-front .brand-name { font-size: 44px; }
  .card-front .brand-dot { width: 18px; height: 18px; }
</style>
</head>
<body>

<section class="card card-back" aria-label="Business card back">
  <div class="brand">
    <span class="brand-dot"></span>
    <span class="brand-name">KAJU</span>
  </div>
  <div class="catchphrase">#ALLKAJU</div>
  <div class="website-line">
    <span class="rule left"></span>
    <span class="website">www.kajufreightco.example</span>
    <span class="rule right"></span>
  </div>
  <div class="base-band"><span class="navy"></span><span class="green"></span></div>
</section>

<section class="card card-front" aria-label="Business card front">
  <svg class="wave" width="480" height="291" viewBox="0 0 480 291" aria-hidden="true">
    <path d="M0,0 H480 V8 C420,10 360,20 300,48 C230,80 150,92 0,94 Z" fill="var(--navy)"/>
    <path d="M0,94 C150,94 230,80 300,54 C380,26 440,34 480,54 V68 C440,50 380,44 300,72 C230,98 150,114 0,114 Z" fill="var(--green)"/>
    <path d="M242,38 C300,10 400,12 442,50 C390,24 300,22 242,38 Z" fill="var(--green)"/>
  </svg>
  <div class="person">
    <div class="person-name">Dana Whitcomb</div>
    <div class="person-title">Chairman &amp; CEO</div>
  </div>
  <div class="service">Transportation &amp; Energy Services</div>
  <address class="address">
    4120 North Canyon Ridge<br>Parkway Glendale, AZ 85310
  </address>
  <ul class="contacts">
    <li>
      <svg viewBox="0 0 12 12" aria-hidden="true"><path d="M1,4 C1,2 3,1 6,1 C9,1 11,2 11,4 L8.5,4.5 L8,3 H4 L3.5,4.5 Z M3,5 H9 L10.5,10 H1.5 Z" fill="var(--green)"/></svg>
      <span>623-555-0148</span>
    </li>
    <li>
      <svg viewBox="0 0 12 12" aria-hidden="true"><rect x="0.5" y="2.5" width="11" height="7.5" fill="var(--green)"/><path d="M0.5,2.5 L6,7 L11.5,2.5" stroke="#fff" stroke-width="1" fill="none"/></svg>
      <span>dana@kajufreightco.example</span>
    </li>
    <li>
      <svg viewBox="0 0 12 12" aria-hidden="true"><circle cx="6" cy="6" r="5" fill="var(--green)"/><path d="M1,6 H11 M6,1 C3.5,3.5 3.5,8.5 6,11 M6,1 C8.5,3.5 8.5,8.5 6,11" stroke="#fff" stroke-width="0.8" fill="none"/></svg>
      <span>www.kajufreightco.example</span>
    </li>
  </ul>
  <div class="brand">
    <span class="brand-dot"></span>
    <span class="brand-name">KAJU</span>
  </div>
</section>

</body>
</html>
```